Envelope Design - Winner can do follow-up business

- Varnoko.com is a Swiss-based online store selling business shirts and accessories for business men
- Please visit the webpage to make yourself familiar with the company. Although the text is in German, with Plimbo translator you should be able to understand the main content.
- Our clients are mainly business men between 30 and 60 years old. Mostly with a high income working in the service industry (banking, insurance, lawyers, etc.). Sometimes there wives purchase the shirts for them ;-)
- The colors and the logo are given, as they are also used for the print materials (please see files in attachment)
- I am running several businesses and often need a talented web designer --> the winner gets substantial follow-up business
your task:
-for our company we need a new envelope design
-It should be simple and modern
-please use one of the logos in the followings.
-suprise me :)

```html
<!DOCTYPE html>
<html lang="en">
<head>
<meta charset="utf-8">
<title>Varnoko Envelope Set</title>
<link rel="stylesheet" href="https://fonts.googleapis.com/css2?family=Open+Sans:wght@400;600&display=swap">
<style>
  :root {
    --backdrop: #e9e5df;
    --paper: #ffffff;
    --edge: #4a4a4a;
    --gold: #e6d96c;
    --red: #ec2d24;
    --ink: #1e1e1e;
  }
  * { margin: 0; padding: 0; box-sizing: border-box; }
  html, body { width: 1200px; height: 883px; overflow: hidden; }
  body {
    position: relative;
    background: var(--backdrop);
    font-family: "Open Sans", Arial, sans-serif;
  }
  .envelope {
    position: absolute;
    background: var(--paper);
    width: 958px;
    overflow: hidden;
  }
  .envelope--back { left: 136px; top: 28px; height: 900px; }
  .envelope--middle { left: 47px; top: 197px; height: 451px; border: 1px solid var(--edge); }
  .envelope--front { left: 196px; top: 393px; height: 451px; border: 1px solid var(--edge); }

  .flap { position: absolute; left: 0; top: 0; width: 958px; height: 160px; }
  .wordmark {
    position: absolute;
    font-weight: 600;
    letter-spacing: 3px;
    line-height: 1;
    white-space: nowrap;
  }
  .wordmark--flap-red { color: var(--red); font-size: 40px; left: 0; right: 0; top: 47px; text-align: center; }
  .wordmark--flap-gold { color: var(--gold); font-size: 40px; left: 0; right: 0; top: 50px; text-align: center; }
  .wordmark--front { color: var(--gold); font-size: 42px; left: 32px; top: 103px; }
  .brand-dot {
    position: absolute; left: 140px; top: 36px;
    width: 52px; height: 52px; border-radius: 50%; background: var(--red);
  }

  .contact {
    position: absolute; left: 30px; bottom: 16px;
    display: flex; gap: 34px; align-items: center;
    font-size: 19px; color: var(--ink);
  }
  .contact__item { display: flex; align-items: center; gap: 10px; }
  .contact__item svg { display: block; }
  .corner-curl { position: absolute; right: 0; bottom: 0; }
</style>
</head>
<body>

  <section class="envelope envelope--back" aria-label="Envelope back, coloured flap">
    <svg class="flap" viewBox="0 0 958 160" aria-hidden="true">
      <path d="M0 0 H958 C948 40 945 68 895 78 L520 150 Q479 157 438 150 L63 78 C13 68 10 40 0 0 Z" fill="var(--gold)"/>
    </svg>
    <div class="wordmark wordmark--flap-red">VARNOKO</div>
  </section>

  <section class="envelope envelope--middle" aria-label="Envelope back, white flap">
    <svg class="flap" viewBox="0 0 958 160" aria-hidden="true">
      <path d="M0 0 C12 40 10 68 60 78 L438 150 Q479 157 520 150 L898 78 C948 68 946 40 958 0" fill="none" stroke="var(--edge)" stroke-width="1"/>
    </svg>
    <div class="wordmark wordmark--flap-gold">VARNOKO</div>
  </section>

  <section class="envelope envelope--front" aria-label="Envelope front">
    <div class="brand-dot" aria-hidden="true"></div>
    <div class="wordmark wordmark--front">VARNOKO</div>

    <div class="contact">
      <span class="contact__item">
        <svg width="18" height="26" viewBox="0 0 18 26" aria-hidden="true">
          <path d="M9 0 C4 0 0 4 0 9 C0 15 9 26 9 26 C9 26 18 15 18 9 C18 4 14 0 9 0 Z" fill="var(--red)"/>
          <circle cx="9" cy="9" r="3.5" fill="#fff"/>
        </svg>
        Street Name, City Name, State Zipcode
      </span>
      <span class="contact__item">
        <svg width="24" height="24" viewBox="0 0 24 24" fill="none" stroke="var(--red)" stroke-width="1.4" aria-hidden="true">
          <circle cx="12" cy="12" r="10.5"/>
          <ellipse cx="12" cy="12" rx="4.5" ry="10.5"/>
          <line x1="1.5" y1="12" x2="22.5" y2="12"/>
          <line x1="3" y1="7" x2="21" y2="7"/>
          <line x1="3" y1="17" x2="21" y2="17"/>
        </svg>
        www.varnoko.com
      </span>
    </div>

    <svg class="corner-curl" width="200" height="170" viewBox="0 0 200 170" aria-hidden="true">
      <path d="M200 0 V170 H0 C90 150 170 110 200 0 Z" fill="var(--gold)"/>
      <path d="M200 0 C175 50 160 70 100 70 C115 120 60 160 0 170 C100 160 170 110 200 0 Z" fill="var(--red)"/>
    </svg>
  </section>

</body>
</html>
```